Modern Business Card For A Digital Advertising Company

I'll be print on the Pell Prints Velour paper http://us.pellprints.com/products/velour/business-cards.html
Need's to be modern and use the color palette of the logo or gray scales. I think integrating the pixelation of the logo in to the card and having it wrap from one side to the other could be interesting. My company provides ad operations, web development, and number of other services to websites around the world. You can see my website at http://www.zantorhq.com
Contact info on the card needs to have
Owen Lasko
President
p.318.204.6637
owen@zantorhq.com
http://www.zantorhq.com
Doesn't necessarily need to be in that order
Website owners
Business

```html
<!DOCTYPE html>
<html lang="en">
<head>
<meta charset="utf-8">
<title>Zantor HQ — Business Card</title>
<link rel="stylesheet" href="https://fonts.googleapis.com/css2?family=Open+Sans:wght@400;700;800&display=swap">
<style>
  :root {
    --lime: #8de01c;
    --lime-soft: #b4ee6a;
    --ink: #363a36;
    --rule: #3a3a3a;
    --paper: #ffffff;
  }
  * { margin: 0; padding: 0; box-sizing: border-box; }
  html, body {
    width: 1200px;
    height: 843px;
    overflow: hidden;
    background: var(--paper);
  }
  .card {
    position: relative;
    width: 1200px;
    height: 843px;
    background: var(--paper);
    font-family: "Open Sans", Arial, sans-serif;
    color: var(--ink);
  }
  .brand {
    position: absolute;
    left: 12px;
    top: 0;
    width: 480px;
  }
  .brand-name {
    display: block;
    font-weight: 800;
    font-size: 92px;
    line-height: 0.9;
    letter-spacing: 1px;
    color: var(--ink);
    text-transform: uppercase;
  }
  .pixel-band {
    position: absolute;
    background: linear-gradient(90deg, var(--lime), var(--lime-soft), var(--lime));
  }
  .pixel-band--top {
    left: 506px;
    top: 7px;
    width: 672px;
    height: 102px;
  }
  .pixel-band--side {
    left: 11px;
    top: 200px;
    width: 100px;
    height: 363px;
    background: linear-gradient(180deg, var(--lime), var(--lime-soft), var(--lime));
  }
  .contact {
    position: absolute;
    left: 533px;
    top: 454px;
    padding-left: 30px;
    border-left: 2px solid var(--rule);
    font-size: 43px;
    line-height: 61px;
    white-space: nowrap;
  }
  .contact-name {
    font-weight: 700;
    font-size: 42px;
  }
</style>
</head>
<body>
  <div class="card">
    <div class="brand">
      <span class="brand-name">Zantor<br>HQ</span>
    </div>

    <div class="pixel-band pixel-band--top" role="img" aria-label="Lime green pixel-square pattern running along the top edge"></div>
    <div class="pixel-band pixel-band--side" role="img" aria-label="Lime green pixel-square pattern running down the left edge"></div>

    <div class="contact">
      <p class="contact-name">Owen Lasko</p>
      <p class="contact-title">President</p>
      <p class="contact-phone">p.318.204.6637</p>
      <p class="contact-email">owen@zantorhq.com</p>
      <p class="contact-web">http://www.zantorhq.com</p>
    </div>
  </div>
</body>
</html>
```